We Buy Houses Postcard Design

Harborline Asset Partners is one of Baltimore‘s top real estate investing groups because we treat buyers and sellers like real people; not like numbers on a spreadsheet. We specialize in buying distressed properties including multi-family, commercial, retail, single family, and bank REO’s from sellers who need to sell fast. Our website is www.harborlineassetpartners.com. Our phone number is (555) 274-1916. Both need to be on the card. Front and back sides are to be printed. Front full color, back black and white. We want our logo on the design somewhere. The logo can be found on the website. If you need the original files ask me for them. See attached as examples. Return address should be 587 W Tessaly Ave, Suite 319, Baltimore, MD 21209. My name is Marcus. Address label is 1" x 2-5/8". Please leave room for it and postage on the back side.

Industry/Entity Type

Real Estate

```html
<!DOCTYPE html>
<html lang="en">
<head>
<meta charset="utf-8">
<title>Harborline Asset Partners – We Buy Houses Postcard</title>
<link rel="stylesheet" href="https://fonts.googleapis.com/css2?family=Archivo+Black&family=Arimo:wght@400;700&display=swap">
<style>
  :root {
    --red: #ee1c25;
    --white: #ffffff;
    --ink: #1a1a1a;
    --backdrop: #d9d9d9;
    --card-shadow: rgba(0, 0, 0, 0.25);
  }
  * { box-sizing: border-box; margin: 0; padding: 0; }
  html, body {
    width: 1200px;
    height: 900px;
    overflow: hidden;
    background: var(--backdrop);
  }
  .canvas {
    position: relative;
    width: 1200px;
    height: 900px;
  }
  .postcard {
    position: absolute;
    width: 620px;
    height: 413px;
    background: var(--white);
    box-shadow: 0 6px 18px var(--card-shadow);
    overflow: hidden;
  }

  /* Front side */
  .postcard--front { left: 70px; top: 30px; }
  .front__headline {
    position: absolute;
    left: 34px;
    top: 18px;
    font-family: "Archivo Black", "Arial Black", sans-serif;
    color: var(--red);
    font-size: 92px;
    line-height: 0.92;
    letter-spacing: -1px;
  }
  .front__tagline {
    position: absolute;
    left: 36px;
    top: 198px;
    font-family: "Archivo Black", "Arial Black", sans-serif;
    color: var(--red);
    font-size: 29px;
    letter-spacing: 1.5px;
    white-space: nowrap;
  }
  .front__phone-band {
    position: absolute;
    left: 28px;
    right: 28px;
    top: 252px;
    height: 104px;
    background: var(--red);
    display: flex;
    align-items: center;
    justify-content: center;
  }
  .front__phone {
    font-family: "Archivo Black", "Arial Black", sans-serif;
    color: var(--white);
    font-size: 60px;
    letter-spacing: 5px;
    white-space: nowrap;
  }

  /* Back side */
  .postcard--back { left: 510px; top: 457px; }
  .back__message {
    position: absolute;
    left: 30px;
    top: 22px;
    width: 310px;
    font-family: "Arimo", Arial, sans-serif;
    color: var(--ink);
    font-size: 12.5px;
    line-height: 1.35;
  }
  .brand {
    display: flex;
    align-items: center;
    gap: 7px;
    margin: 0 0 10px 60px;
  }
  .brand__mark {
    width: 14px;
    height: 14px;
    background: var(--red);
  }
  .brand__name {
    font-weight: 700;
    font-size: 14px;
    color: var(--ink);
  }
  .offer-box {
    border: 1.5px solid var(--red);
    padding: 4px 8px;
    margin: 4px 0 6px;
    list-style: none;
  }
  .offer-box li::before { content: "- "; }
  .back__return {
    position: absolute;
    left: 30px;
    top: 268px;
    font-family: "Arimo", Arial, sans-serif;
    color: var(--ink);
    font-size: 10.5px;
    line-height: 1.35;
  }
  .back__return-phone {
    font-weight: 700;
    font-size: 14px;
  }
  .back__urgent {
    position: absolute;
    right: 40px;
    bottom: 40px;
    width: 270px;
    height: 56px;
    background: var(--red);
    display: flex;
    align-items: center;
    justify-content: center;
    font-family: "Arimo", Arial, sans-serif;
    font-weight: 700;
    color: var(--white);
    font-size: 22px;
    letter-spacing: 4px;
  }
</style>
</head>
<body>
<main class="canvas">

  <section class="postcard postcard--front" aria-label="Postcard front">
    <h1 class="front__headline">WE BUY<br>HOUSES</h1>
    <p class="front__tagline">Any Condition – Fast Closing</p>
    <div class="front__phone-band">
      <span class="front__phone">555-274-1916</span>
    </div>
  </section>

  <section class="postcard postcard--back" aria-label="Postcard back">
    <div class="back__message">
      <div class="brand">
        <span class="brand__mark"></span>
        <span class="brand__name">Harborline Asset Partners</span>
      </div>
      <p>Are you looking to sell your house,<br>land or commercial property?<br>We offer:</p>
      <ul class="offer-box">
        <li>CASH for your house “AS-IS”</li>
        <li>No inspections or contingencies</li>
        <li>Fast and flexible closing</li>
        <li>No need to fix or clean out your home</li>
      </ul>
      <p>There are never any obligations.<br>If you're interested, please contact us.<br>We look forward to hearing from you!</p>
    </div>
    <address class="back__return" style="font-style: normal;">
      Harborline Asset Partners, LLC<br>
      www.harborlineassetpartners.com<br>
      587 W Tessaly Ave, Suite 319, Baltimore, MD 21209<br>
      <span class="back__return-phone">(555) 274-1916</span>
    </address>
    <div class="back__urgent">URGENT NOTICE</div>
  </section>

</main>
</body>
</html>
```